Birchline Septic Solutions

Would like to see some single sided ones but would also like to see some double sided with one sided only being the logo. Owners name is Colin Vandro. Phone number is 555-214-0387
Services are pumping, inspections, installs, and repairs

Contact Information for Business Card

555-241-0387 Colin Vandro Greenfield, OH

```html
<!DOCTYPE html>
<html lang="en">
<head>
<meta charset="utf-8">
<title>Birchline Septic Solutions — Business Cards</title>
<link href="https://fonts.googleapis.com/css2?family=Montserrat:wght@300;400;700;800&display=swap" rel="stylesheet">
<style>
  :root {
    --backdrop: #4a4a4a;
    --backdrop-dark: #3a3a3a;
    --card: #161616;
    --teal: #2ebfb6;
    --white: #ffffff;
    --emboss: #1d1d1d;
    --emboss-light: #262626;
    --card-w: 540px;
    --card-h: 309px;
  }
  * { box-sizing: border-box; margin: 0; padding: 0; }
  html, body { width: 1200px; height: 801px; overflow: hidden; }
  body {
    background: radial-gradient(ellipse at 40% 30%, var(--backdrop), var(--backdrop-dark));
    font-family: "Montserrat", sans-serif;
    display: flex;
    align-items: center;
    justify-content: center;
    gap: 40px;
  }
  .card {
    position: relative;
    width: var(--card-w);
    height: var(--card-h);
    background: var(--card);
    border-bottom: 4px solid var(--teal);
    box-shadow: 0 18px 40px rgba(0,0,0,.45);
    overflow: hidden;
  }

  /* Front */
  .front__tab {
    position: absolute;
    top: 0; right: 24px;
    width: 44px; height: 22px;
    background: var(--teal);
  }
  .front__person {
    position: absolute;
    top: 40px; right: 28px;
    text-align: right;
  }
  .front__name {
    color: var(--teal);
    font-weight: 800;
    font-size: 28px;
    letter-spacing: .5px;
  }
  .front__role {
    color: var(--white);
    font-weight: 300;
    font-size: 13px;
    margin-top: 2px;
  }
  .front__brand {
    position: absolute;
    left: 34px; top: 118px;
    display: flex;
    align-items: center;
    gap: 10px;
  }
  .front__brand-mark {
    width: 14px; height: 14px;
    background: var(--teal);
  }
  .front__brand-name {
    color: var(--white);
    font-weight: 800;
    font-size: 21px;
    letter-spacing: .5px;
    line-height: 1.1;
  }
  .front__address {
    position: absolute;
    left: 58px; top: 172px;
    color: var(--white);
    font-weight: 400;
    font-size: 14px;
    line-height: 1.35;
  }
  .front__contacts {
    position: absolute;
    left: 34px; bottom: 22px;
    list-style: none;
    color: var(--white);
    font-size: 14px;
    line-height: 1.6;
  }
  .front__contacts li { display: flex; align-items: center; gap: 10px; }
  .front__contacts svg { width: 13px; height: 13px; fill: var(--teal); flex: none; }

  /* Back */
  .back__brand {
    position: absolute;
    left: 0; right: 0; top: 78px;
    text-align: center;
    color: var(--emboss);
    font-weight: 800;
    font-size: 40px;
    letter-spacing: 2px;
    line-height: 1.15;
    text-shadow: 0 1px 0 var(--emboss-light), 0 -1px 0 #0d0d0d;
  }
  .back__band {
    position: absolute;
    left: 0; right: 0; bottom: 42px;
    height: 30px;
    background: var(--teal);
    color: var(--white);
    font-size: 16px;
    font-weight: 400;
    display: flex;
    align-items: center;
    justify-content: center;
  }
</style>
</head>
<body>
  <section class="card front" aria-label="Business card front">
    <div class="front__tab"></div>
    <div class="front__person">
      <div class="front__name">Colin Vandro</div>
      <div class="front__role">Owners</div>
    </div>
    <div class="front__brand">
      <span class="front__brand-mark"></span>
      <span class="front__brand-name">Birchline<br>Septic Solutions</span>
    </div>
    <address class="front__address" style="font-style:normal">
      Your address, City<br>State, Zip 1234
    </address>
    <ul class="front__contacts">
      <li>
        <svg viewBox="0 0 24 24" aria-hidden="true"><path d="M6.6 10.8a15.1 15.1 0 0 0 6.6 6.6l2.2-2.2a1 1 0 0 1 1-.25 11.4 11.4 0 0 0 3.6.57 1 1 0 0 1 1 1V20a1 1 0 0 1-1 1A17 17 0 0 1 3 4a1 1 0 0 1 1-1h3.5a1 1 0 0 1 1 1c0 1.25.2 2.45.57 3.57a1 1 0 0 1-.25 1z"/></svg>
        555-214-0387
      </li>
      <li>
        <svg viewBox="0 0 24 24" aria-hidden="true"><path d="M2 5h20v14H2zm2 2v.4l8 5 8-5V7l-8 5z"/></svg>
        info@yourgmail.com
      </li>
      <li>
        <svg viewBox="0 0 24 24" aria-hidden="true"><path d="M12 2a10 10 0 1 0 0 20 10 10 0 0 0 0-20zm6.9 6h-3a15 15 0 0 0-1.3-3.9A8 8 0 0 1 18.9 8zM12 4c.8 1.2 1.5 2.5 1.9 4h-3.8c.4-1.5 1.1-2.8 1.9-4zM4.3 14a8 8 0 0 1 0-4h3.4a16 16 0 0 0 0 4zm.8 2h3a15 15 0 0 0 1.3 3.9A8 8 0 0 1 5.1 16zm3-8h-3a8 8 0 0 1 4.3-3.9A15 15 0 0 0 8.1 8zM12 20c-.8-1.2-1.5-2.5-1.9-4h3.8c-.4 1.5-1.1 2.8-1.9 4zm2.3-6H9.7a14 14 0 0 1 0-4h4.6a14 14 0 0 1 0 4zm.3 5.9a15 15 0 0 0 1.3-3.9h3a8 8 0 0 1-4.3 3.9zm1.7-5.9a16 16 0 0 0 0-4h3.4a8 8 0 0 1 0 4z"/></svg>
        www.yourwebsite.com
      </li>
    </ul>
  </section>

  <section class="card back" aria-label="Business card back">
    <div class="back__brand">Birchline<br>Septic Solutions</div>
    <div class="back__band">Services are pumping, inspections, installs, and repairs</div>
  </section>
</body>
</html>
```